Nivel Crest - Powerpoint Templates

We are a consultancy to help builders to optimize their planning in order to save building costs. For that reason we need templates for teasers and presentations where we offer our services, show our team and their capacities and present workflows, organization charts, price lists etc.

```html
<!DOCTYPE html>
<html lang="en">
<head>
<meta charset="utf-8">
<title>Nivel Crest – Presentation Templates</title>
<link href="https://fonts.googleapis.com/css2?family=Audiowide&family=Roboto:wght@400;500;700&display=swap" rel="stylesheet">
<style>
:root{
  --gold:#b97f2c;
  --gold-dark:#a06a22;
  --yellow:#f2cf72;
  --yellow-soft:#f6dd97;
  --ink:#1c1c1c;
  --text:#555;
  --muted:#8a8a8a;
  --page:#ececec;
  --white:#fff;
  --red:#d9534f;
  --navy:#274b7a;
}
*{box-sizing:border-box;margin:0;padding:0}
html,body{width:1200px;height:4608px;overflow:hidden}
body{background:var(--page);font-family:"Roboto",sans-serif;color:var(--ink);position:relative}
.slide{position:absolute;left:79px;width:1042px;height:587px;background:var(--white);overflow:hidden;box-shadow:0 2px 10px rgba(0,0,0,.08)}
.side-bar{position:absolute;left:0;top:0;width:118px;height:587px;background:var(--gold);border-bottom-right-radius:118px 110px}
.brand{position:absolute;font-family:"Audiowide",sans-serif;color:var(--gold);font-size:26px;letter-spacing:1px;text-align:center;white-space:nowrap}
.heading{position:absolute;font-family:"Audiowide",sans-serif;color:var(--ink);letter-spacing:2px;text-transform:uppercase;white-space:nowrap}
.photo{position:absolute}
.p-warm{background:linear-gradient(135deg,#c9b79a,#8d7a62 55%,#5e5044)}
.p-site{background:linear-gradient(160deg,#d9c3a0,#b08a5a 50%,#6f5a45)}
.p-desk{background:linear-gradient(145deg,#e4ded6,#b8aca0 60%,#7d7064)}
.p-sky{background:linear-gradient(170deg,#e8e4dc,#b7b0a5 55%,#6c6a67)}
.p-avatar{background:linear-gradient(160deg,#d5d5d5,#8e8e8e)}
.dots{position:absolute;display:flex;gap:8px}
.dot{width:26px;height:26px;border-radius:50%;background:var(--gold)}
.dot.line{width:18px;height:18px;background:none;border:1.5px solid var(--gold)}
</style>
</head>
<body>

<!-- Welcome -->
<section class="slide" style="top:84px">
  <svg width="1042" height="587" style="position:absolute;left:0;top:0">
    <polygon points="0,0 161,0 408,587 0,587" fill="var(--yellow)"/>
    <polygon points="78,250 100,242 270,560 248,568" fill="var(--gold)"/>
    <polygon points="935,0 990,0 1042,70 1042,150" fill="var(--gold)"/>
    <polygon points="990,0 1042,0 1042,70" fill="var(--yellow)"/>
  </svg>
  <div class="photo p-site" role="img" aria-label="Engineers in safety vests reviewing plans on a construction site with a crane" style="left:11px;top:68px;width:626px;height:492px;clip-path:polygon(0 0,429px 0,626px 492px,214px 492px)"></div>
  <div class="brand" style="left:733px;top:92px;width:260px">NIVEL CREST</div>
  <div class="heading" style="right:54px;top:214px;font-size:28px;color:var(--gold)">Welcome to</div>
  <div class="heading" style="right:54px;top:266px;font-size:42px">Nivel Crest</div>
  <p style="position:absolute;right:54px;top:330px;width:460px;text-align:right;font-size:18px;line-height:27px;color:var(--ink)">Lorem ipsum dolor sit amet adipiscing elit sed do eiusmod tempor incididunt ut labore et dolore</p>
  <div class="dots" style="right:54px;top:394px"><span class="dot"></span><span class="dot"></span><span class="dot"></span></div>
</section>

<!-- Services -->
<section class="slide" style="top:726px">
  <div class="side-bar"></div>
  <div class="brand" style="left:391px;top:96px;width:260px">NIVEL CREST</div>
  <div class="heading" style="left:0;width:1042px;text-align:center;top:166px;font-size:28px">Our Services</div>
  <div class="photo p-desk" role="img" aria-label="Hands working over construction drawings with tools" style="left:55px;top:240px;width:222px;height:214px"></div>
  <div class="photo p-site" role="img" aria-label="Construction team in hard hats reviewing papers" style="left:292px;top:240px;width:222px;height:214px"></div>
  <div class="photo p-sky" role="img" aria-label="Two colleagues looking at a laptop over plans" style="left:528px;top:240px;width:222px;height:214px"></div>
  <div class="photo p-site" role="img" aria-label="Engineers on a building site" style="left:764px;top:240px;width:222px;height:214px"></div>
  <div style="position:absolute;top:466px;left:55px;width:931px;display:flex;justify-content:space-between;font-size:16px;font-weight:500">
    <span style="width:222px;text-align:center">Lorem ipsum dolor</span><span style="width:222px;text-align:center">Lorem ipsum dolor</span><span style="width:222px;text-align:center">Lorem ipsum dolor</span><span style="width:222px;text-align:center">Lorem ipsum dolor</span>
  </div>
</section>

<!-- Teasers -->
<section class="slide" style="top:1368px">
  <div class="side-bar"></div>
  <div class="photo p-desk" role="img" aria-label="Handshake over a desk with a hard hat and blueprints" style="left:55px;top:132px;width:376px;height:208px"></div>
  <div class="photo p-site" role="img" aria-label="Construction workers holding a plan on site" style="left:347px;top:243px;width:202px;height:252px;border:4px solid #fff"></div>
  <div class="photo p-warm" role="img" aria-label="Team hands over rolled blueprints" style="left:55px;top:393px;width:279px;height:152px"></div>
  <div class="brand" style="left:737px;top:88px;width:260px">NIVEL CREST</div>
  <div class="heading" style="left:622px;top:140px;font-size:27px;line-height:34px">Easers and<br>Presentations</div>
  <p style="position:absolute;left:622px;top:232px;width:349px;font-size:15.5px;line-height:26.8px;color:var(--text);text-align:justify">Lorem ipsumied consectetuer adipiscing sed Deiusmod tempor incididunt ut labore et dolore magna aliqua. Ut enim minim veniam nostrud exercitation ullamco laboris nisi aliquip ex ea commodo consequat. aute irure dolor in reprehenderit voluptate velit esse cillum dolore eu fugiat nulla pariatur. Excepteur occaecat cupidatat proident sunt in culpa qui officia laborumquis nostrud exercitation ulaboris nisi aliquip commodo consequat Duis aute irure dolor in reprehenderit ined voluptate velited.</p>
</section>

<!-- Team -->
<section class="slide" style="top:2010px">
  <div class="side-bar"></div>
  <div class="heading" style="left:165px;top:56px;font-size:27px">Our Team</div>
  <p style="position:absolute;left:165px;top:98px;width:520px;font-size:15px;line-height:22px;color:var(--text)">Lorem ipsum dolor sit amet, consectetur adipiscing elit sed do eiusmod tempor incididunt labore et dolore magna aliqua enim ad minim .</p>
  <div class="brand" style="left:737px;top:88px;width:260px">NIVEL CREST</div>
  <style>
    .team-card{position:absolute;top:206px;width:222px;height:327px;background:#fff;border:2px solid #e4e4e4;border-radius:8px;text-align:center}
    .team-card .avatar{width:92px;height:92px;border-radius:50%;margin:24px auto 14px}
    .team-card h4{font-size:10.5px;font-weight:700;margin-bottom:9px}
    .team-card .role{font-size:10.5px;font-weight:700;margin-bottom:10px}
    .team-card p{font-size:10px;line-height:16px;color:var(--text);padding:0 18px}
    .team-card .dots{position:static;justify-content:center;gap:4px;margin-top:12px}
  </style>
  <article class="team-card" style="left:59px"><div class="avatar p-avatar" role="img" aria-label="Portrait of a team member"></div><h4>ALEX MORAN</h4><div class="role">PARTNER</div><p>Lorem ipsum dolor amet, consectetur adipiscing elit, sed eiusmod tempor incididunt ut labore et dolore magna aliqua. Ut enim ad minim veniam, quis nostrud exercitation ullamco</p><div class="dots"><span class="dot line"></span><span class="dot line"></span><span class="dot line"></span></div></article>
  <article class="team-card" style="left:293px"><div class="avatar p-avatar" role="img" aria-label="Portrait of a team member"></div><h4>ALEX MORAN</h4><div class="role">PARTNER</div><p>Lorem ipsum dolor amet, consectetur adipiscing elit, sed eiusmod tempor incididunt ut labore et dolore magna aliqua. Ut enim ad minim veniam, quis nostrud exercitation ullamco</p><div class="dots"><span class="dot line"></span><span class="dot line"></span><span class="dot line"></span></div></article>
  <article class="team-card" style="left:527px"><div class="avatar p-avatar" role="img" aria-label="Portrait of a team member"></div><h4>SAM KELLER</h4><div class="role">PARTNER</div><p>Lorem ipsum dolor amet, consectetur adipiscing elit, sed eiusmod tempor incididunt ut labore et dolore magna aliqua. Ut enim ad minim veniam, quis nostrud exercitation ullamco</p><div class="dots"><span class="dot line"></span><span class="dot line"></span><span class="dot line"></span></div></article>
  <article class="team-card" style="left:762px"><div class="avatar p-avatar" role="img" aria-label="Portrait of a team member"></div><h4>SAM KELLER</h4><div class="role">PARTNER</div><p>Lorem ipsum dolor amet, consectetur adipiscing elit, sed eiusmod tempor incididunt ut labore et dolore magna aliqua. Ut enim ad minim veniam, quis nostrud exercitation ullamco</p><div class="dots"><span class="dot line"></span><span class="dot line"></span><span class="dot line"></span></div></article>
</section>

<!-- Organization chart -->
<section class="slide" style="top:2652px">
  <div class="heading" style="left:0;width:1042px;text-align:center;top:94px;font-size:28px">Organization Charts</div>
  <p style="position:absolute;left:55px;width:932px;top:142px;text-align:center;font-size:15.5px;line-height:26px;color:var(--text)">Lorem ipsum dolor sit amet, consectetur adipiscing elit, sed do eiusmod tempor incididunt ut labore et dolore magna aliqua. Ut enim ad minim veniam, quis nostrud exercitation ullamco laboris nisi ut aliquip ex ea commodo consequat.</p>
  <svg width="760" height="587" style="position:absolute;left:0;top:0;font-family:Roboto,sans-serif" font-size="9" fill="var(--muted)">
    <g text-anchor="end">
      <text x="100" y="255">100</text><text x="100" y="283">90</text><text x="100" y="312">80</text><text x="100" y="340">70</text><text x="100" y="369">60</text><text x="100" y="398">50</text><text x="100" y="426">40</text><text x="100" y="455">30</text><text x="100" y="483">20</text><text x="100" y="512">10</text>
    </g>
    <g text-anchor="middle">
      <text x="132" y="546">Jan</text><text x="182" y="546">Feb</text><text x="231" y="546">Mar</text><text x="281" y="546">Apr</text><text x="331" y="546">May</text><text x="379" y="546">Jun</text><text x="429" y="546">Jul</text><text x="479" y="546">Aug</text><text x="529" y="546">Sep</text><text x="578" y="546">Oct</text><text x="628" y="546">Nov</text><text x="678" y="546">Dec</text>
    </g>
    <g fill="var(--yellow)">
      <rect x="125" y="424" width="16" height="114"/><rect x="221" y="481" width="16" height="57"/><rect x="276" y="338" width="16" height="200"/><rect x="341" y="409" width="16" height="129"/><rect x="427" y="286" width="16" height="252"/><rect x="509" y="401" width="16" height="137"/><rect x="545" y="372" width="16" height="166"/><rect x="606" y="409" width="16" height="129"/><rect x="669" y="446" width="16" height="92"/>
    </g>
    <g fill="var(--gold)">
      <rect x="158" y="395" width="16" height="143"/><rect x="243" y="366" width="16" height="172"/><rect x="303" y="446" width="16" height="92"/><rect x="371" y="481" width="16" height="57"/><rect x="454" y="315" width="16" height="223"/><rect x="486" y="258" width="16" height="280"/><rect x="574" y="446" width="16" height="92"/><rect x="654" y="252" width="16" height="286"/>
    </g>
  </svg>
  <div style="position:absolute;left:774px;top:274px;width:213px;height:35px;background:var(--yellow);color:#fff;font-size:11px;font-weight:700;display:flex;align-items:center;justify-content:center">PRODUCT 1</div>
  <p style="position:absolute;left:774px;top:322px;width:213px;font-size:9.5px;line-height:14px;color:var(--muted);text-align:justify;text-align-last:center">Lorem ipsum dolor sit amet, consectetur adipiscing elit, sed do eiusmod tempor incididunt ut labore et dolore magna aliqua. Ut enim ad minim veniam, quis nostrud exercitation ullamco</p>
  <div style="position:absolute;left:774px;top:420px;width:213px;height:36px;background:var(--gold);color:#fff;font-size:11px;font-weight:700;display:flex;align-items:center;justify-content:center">PRODUCT 2</div>
  <p style="position:absolute;left:774px;top:468px;width:213px;font-size:9.5px;line-height:14px;color:var(--muted);text-align:justify;text-align-last:center">Lorem ipsum dolor sit amet, consectetur adipiscing elit, sed do eiusmod tempor incididunt ut labore et dolore magna aliqua. Ut enim ad minim veniam, quis nostrud exercitation ullamco</p>
</section>

<!-- Price lists -->
<section class="slide" style="top:3294px">
  <div class="side-bar"></div>
  <div class="brand" style="left:391px;top:96px;width:260px">NIVEL CREST</div>
  <div class="heading" style="left:0;width:1042px;text-align:center;top:166px;font-size:28px">Price Lists</div>
  <style>
    .price-card{position:absolute;background:#fff;box-shadow:0 4px 18px rgba(0,0,0,.1);text-align:center;padding-top:26px;overflow:hidden}
    .price-card h3{font-size:20px;font-weight:500;color:var(--ink)}
    .price-card .price{font-size:19px;font-weight:700;color:var(--gold);margin:6px 0 16px}
    .price-card ul{list-style:none;text-align:left;padding-left:34px}
    .price-card li{font-size:11px;color:var(--text);margin-bottom:14px;display:flex;align-items:center;gap:10px}
    .price-card li::before{content:"";width:11px;height:11px;border-radius:50%;background:var(--gold)}
    .price-card .cta{display:inline-block;margin-top:24px;background:var(--gold);color:#fff;font-size:11px;font-weight:700;padding:10px 16px;border-radius:2px}
    .price-card.featured{background:var(--gold)}
    .price-card.featured h3,.price-card.featured .price,.price-card.featured li{color:#fff}
    .price-card.featured li::before{background:#fff}
    .price-card.featured .cta{background:#fff;color:var(--gold)}
  </style>
  <div class="price-card" style="left:172px;top:250px;width:237px;height:263px"><h3>Lorem ipsum dolor</h3><div class="price">FREE</div><ul><li>Lorem ipsum dolor sit amet</li><li>Lorem ipsum dolor sit amet</li><li>Lorem ipsum dolor sit amet</li></ul><span class="cta">GET STARTED</span></div>
  <div class="price-card featured" style="left:442px;top:227px;width:241px;height:265px"><h3>Lorem ipsum dolor</h3><div class="price">FREE</div><ul><li>Lorem ipsum dolor sit amet</li><li>Lorem ipsum dolor sit amet</li><li>Lorem ipsum dolor sit amet</li></ul><span class="cta">GET STARTED</span>
    <svg width="70" height="70" style="position:absolute;right:0;bottom:0"><circle cx="56" cy="56" r="40" fill="rgba(255,255,255,.15)"/><circle cx="56" cy="56" r="24" fill="rgba(255,255,255,.2)"/></svg></div>
  <div class="price-card" style="left:713px;top:250px;width:238px;height:263px"><h3>Lorem ipsum dolor</h3><div class="price">FREE</div><ul><li>Lorem ipsum dolor sit amet</li><li>Lorem ipsum dolor sit amet</li><li>Lorem ipsum dolor sit amet</li></ul><span class="cta">GET STARTED</span></div>
</section>

<!-- Workflows -->
<section class="slide" style="top:3936px">
  <div class="side-bar"></div>
  <div class="heading" style="left:166px;top:54px;font-size:27px">Present Workflows</div>
  <div class="brand" style="left:737px;top:88px;width:260px">NIVEL CREST</div>
  <div style="position:absolute;left:318px;top:161px;width:474px;height:82px;background:#fff;border:2px solid #e2e2e2;border-radius:6px;box-shadow:0 3px 12px rgba(0,0,0,.08);display:flex;align-items:center;justify-content:center;text-align:center;font-size:15.5px;font-weight:500;line-height:22px">LOREM IPSUM DOLOR SIT AMET CONSECTETUR<br>ADIPISCING SED DO EIUSMOD TEMPOR</div>
  <svg width="1042" height="587" style="position:absolute;left:0;top:0" fill="none" stroke-width="2.5">
    <path d="M520 263 V297 H313 V340" stroke="var(--red)"/>
    <path d="M549 263 V340" stroke="var(--gold)"/>
    <path d="M588 263 V297 H796 V340" stroke="var(--navy)"/>
    <circle cx="520" cy="257" r="6" stroke="var(--red)" fill="#fff"/>
    <circle cx="549" cy="257" r="6" stroke="var(--gold)" fill="#fff"/>
    <circle cx="588" cy="257" r="6" stroke="var(--navy)" fill="#fff"/>
    <rect x="218" y="340" width="190" height="186" rx="22" stroke="var(--red)"/>
    <rect x="460" y="340" width="187" height="186" rx="22" stroke="var(--gold)"/>
    <rect x="701" y="340" width="190" height="186" rx="22" stroke="var(--navy)"/>
    <circle cx="218" cy="433" r="6" stroke="var(--red)" fill="#fff"/><circle cx="408" cy="433" r="6" stroke="var(--red)" fill="#fff"/>
    <circle cx="460" cy="433" r="6" stroke="var(--gold)" fill="#fff"/><circle cx="647" cy="433" r="6" stroke="var(--gold)" fill="#fff"/>
    <circle cx="701" cy="433" r="6" stroke="var(--navy)" fill="#fff"/><circle cx="891" cy="433" r="6" stroke="var(--navy)" fill="#fff"/>
  </svg>
  <style>
    .flow-card{position:absolute;top:356px;width:158px;height:154px;background:#fff;border-radius:14px;box-shadow:0 4px 14px rgba(0,0,0,.12);text-align:center;padding-top:18px}
    .flow-card h4{font-size:15px;font-weight:500;margin:6px 0 4px}
    .flow-card p{font-size:9.5px;line-height:14px;color:var(--text);padding:0 14px}
  </style>
  <div class="flow-card" style="left:234px"><svg width="40" height="38" fill="none" stroke="var(--red)" stroke-width="2"><rect x="8" y="14" width="24" height="18" rx="2"/><path d="M14 14 V9 H26 V14 M8 22 H32"/></svg><h4>LOREM IPSUM</h4><p>Lorem ipsum dolor sit amet, consectetur adipiscing elit, sed do eiusmod tempor</p></div>
  <div class="flow-card" style="left:474px"><svg width="40" height="42" fill="none" stroke="var(--gold)" stroke-width="2"><circle cx="20" cy="12" r="7"/><path d="M20 19 V26 M8 38 H32 M12 38 V30 H28 V38"/></svg><h4>LOREM IPSUM</h4><p>Lorem ipsum dolor sit amet, consectetur adipiscing elit, sed do eiusmod tempor</p></div>
  <div class="flow-card" style="left:717px"><svg width="40" height="38" fill="none" stroke="var(--navy)" stroke-width="2"><circle cx="20" cy="15" r="8"/><circle cx="20" cy="15" r="3"/><path d="M6 30 Q20 24 34 30"/></svg><h4>LOREM IPSUM</h4><p>Lorem ipsum dolor sit amet, consectetur adipiscing elit, sed do eiusmod tempor</p></div>
</section>

</body>
</html>
```